Realty Group Needs Classy, Contemporary Letterhead Design

We need a letterhead design for a new realty company located in NY, USA. We buy investment properties to rehabilitate and or keep in our rental portfolio.

```html
<!DOCTYPE html>
<html lang="en">
<head>
<meta charset="utf-8">
<title>Halden Realty Group – Letterhead</title>
<link href="https://fonts.googleapis.com/css2?family=Open+Sans:wght@400;600;700;800&family=Caveat:wght@500&display=swap" rel="stylesheet">
<style>
  :root {
    --backdrop: #ebebeb;
    --paper: #ffffff;
    --brand-purple: #4a2386;
    --brand-grey: #8a8a8a;
    --ink: #2b2b2b;
    --ink-soft: #5a5a5a;
    --script-ink: #1e2a5a;
  }
  * { box-sizing: border-box; margin: 0; padding: 0; }
  html, body {
    width: 1200px; height: 795px; overflow: hidden;
    background: var(--backdrop);
    font-family: "Open Sans", Arial, sans-serif;
    color: var(--ink);
  }
  .letterhead {
    position: absolute; left: 338px; top: 28px;
    width: 524px; height: 740px;
    background: var(--paper);
    box-shadow: 0 2px 10px rgba(0,0,0,0.12);
    overflow: hidden;
  }
  .brand {
    position: absolute; left: 44px; top: 52px;
    display: flex; align-items: center; gap: 6px;
  }
  .brand-mark { width: 10px; height: 10px; background: var(--brand-purple); }
  .brand-name {
    font-size: 15px; font-weight: 800; color: var(--brand-purple);
    letter-spacing: 0.3px; line-height: 1;
  }
  .contact-list {
    position: absolute; right: 44px; top: 40px;
    list-style: none; font-size: 6.5px; color: var(--ink-soft); line-height: 10px;
  }
  .contact-list li { display: flex; align-items: center; gap: 4px; }
  .contact-icon {
    width: 7px; height: 7px; border-radius: 50%;
    background: var(--brand-purple); flex: none;
  }
  .recipient {
    position: absolute; left: 44px; top: 132px;
    font-size: 8px; line-height: 11px; color: var(--ink);
  }
  .recipient .date { margin-bottom: 10px; }
  .salutation { margin-top: 10px; font-weight: 600; }
  .letter-body {
    position: absolute; left: 44px; top: 250px; width: 300px;
    font-size: 7px; line-height: 10px; color: var(--ink-soft);
  }
  .letter-body p { margin-bottom: 10px; }
  .sign-off {
    position: absolute; left: 360px; top: 176px; width: 130px;
    font-size: 8px; line-height: 11px; color: var(--ink);
  }
  .signature {
    font-family: "Caveat", cursive; font-size: 24px; line-height: 26px;
    color: var(--script-ink); margin: 2px 0 0 -6px;
  }
  .office-address {
    position: absolute; left: 360px; top: 300px;
    display: flex; gap: 5px; font-style: normal;
    font-size: 7px; line-height: 9.5px; color: var(--ink-soft);
  }
  .office-address strong { color: var(--brand-purple); font-weight: 700; display: block; }
  .footer-waves { position: absolute; left: 0; bottom: 0; width: 340px; height: 120px; }
</style>
</head>
<body>
  <main class="letterhead">
    <div class="brand">
      <span class="brand-mark"></span>
      <span class="brand-name">HALDEN REALTY</span>
    </div>

    <ul class="contact-list">
      <li><span class="contact-icon"></span>(212) 555-0148</li>
      <li><span class="contact-icon"></span>(212) 555-0193</li>
      <li><span class="contact-icon"></span>hello@haldenrealty.com</li>
      <li><span class="contact-icon"></span>www.haldenrealtygroup.com</li>
    </ul>

    <section class="recipient">
      <p class="date">January 03, 2017</p>
      <p>Mr. John Doe<br>President<br>AA Corporation<br>111 Street Name, Suite#<br>City, State, 12345</p>
      <p class="salutation">Dear Mr. John,</p>
    </section>

    <section class="letter-body">
      <p>Lorem Ipsum is simply dummy text of the printing and typesetting industry. Lorem Ipsum has been the industry's standard dummy text ever since the 1500s, when an unknown printer took a galley of type and scrambled it to make a type specimen book. It has survived not only five centuries, but also the leap into electronic typesetting, remaining essentially unchanged.</p>
      <p>The standard chunk of Lorem Ipsum used since the 1500s is reproduced below for those interested. Sections 1.10.32 and 1.10.33 from "de Finibus Bonorum et Malorum" by Cicero are also reproduced in their exact original form, accompanied by English versions from the 1914 translation by H. Rackham.</p>
      <p>Lorem Ipsum is simply dummy text of the printing and typesetting industry. Lorem Ipsum has been the industry's standard dummy text ever since the 1500s, when an unknown printer took a galley of type and scrambled it to make a type specimen book. It has survived not only five centuries, but also the leap into electronic typesetting, remaining essentially unchanged. It was popularised in the</p>
    </section>

    <section class="sign-off">
      <p>Sincerely Yours,</p>
      <p class="signature">your name</p>
      <p>Name Last Name<br>Company Name</p>
    </section>

    <address class="office-address">
      <svg width="7" height="10" viewBox="0 0 7 10" aria-hidden="true">
        <path d="M3.5 0C1.6 0 0 1.5 0 3.4 0 6 3.5 10 3.5 10S7 6 7 3.4C7 1.5 5.4 0 3.5 0Z" fill="var(--brand-purple)"/>
        <circle cx="3.5" cy="3.4" r="1.3" fill="#fff"/>
      </svg>
      <span><strong>Halden Realty Group, LLC</strong>Suite 102 Street name, State,<br>Zip 2034, Country</span>
    </address>

    <svg class="footer-waves" viewBox="0 0 340 120" aria-hidden="true">
      <path d="M200 62 C240 28 290 8 340 0 C322 40 290 92 250 120 L200 120 Z" fill="var(--brand-grey)"/>
      <path d="M0 90 C100 90 180 66 246 22 C226 64 212 100 206 120 L0 120 Z" fill="var(--paper)"/>
      <path d="M0 96 C100 96 180 72 240 30 C222 70 208 102 200 120 L0 120 Z" fill="var(--brand-purple)"/>
    </svg>
  </main>
</body>
</html>
```